NEW Modern Sleek Business Card for VR Language Startup

Our startup is using VR to lead the next wave of world language education. We need a two-sided business card that introduces the larger organization (Tarnvale Language Inc) and our contact info on one side and shows the product, Glimwoorld, on the other side.

Side 1 (contact info)= Tarnvale Logo and Contact info (name, title, phone, email)

Side 2 (product)= Glimworld logo, text, and website
Text= Culturally Immersive Language Learning Games
Website= www.glimworld-play.com

Target Market(s)

Education, Technology

Contact Information for Business Card

Contact info will be updated upon approval of the design. For now, put this as a placeholder.

Perry Dunmore
Founder & CEO
pdunmore@quillpost-mail.net
(555)-014-2286

Font styles to use
Other font styles liked:
• Gibson and Century Gothic are the brand fonts

Requirements
Nice to have
• I would love to see cohesion between the design and colors of the two logos. I have attached a few business card designs that I like, so you can get a feel for my preferred style.

```html
<!DOCTYPE html>
<html lang="en">
<head>
<meta charset="utf-8">
<title>Tarnvale Language Inc – Business Card</title>
<link rel="stylesheet" href="https://fonts.googleapis.com/css2?family=Lato:wght@400;700&display=swap">
<style>
  :root {
    --stage: #7b7b7b;
    --dark-top: #242230;
    --dark-bottom: #3a2321;
    --dark-trace: rgba(0, 0, 0, 0.3);
    --blue-top: #1fdcec;
    --blue-mid: #3fa4f2;
    --blue-bottom: #5d6af6;
    --blue-trace: rgba(30, 120, 240, 0.45);
    --white: #ffffff;
    --accent-orange: #f08a3c;
    --accent-red: #f0504a;
    --accent-violet: #7f7df6;
    --accent-cyan: #2fd6e0;
    --rule-dark: rgba(255, 255, 255, 0.18);
    --rule-light: rgba(255, 255, 255, 0.45);
  }

  * { box-sizing: border-box; margin: 0; padding: 0; }

  html, body {
    width: 1200px;
    height: 866px;
    overflow: hidden;
  }

  body {
    background: var(--stage);
    font-family: "Lato", "Century Gothic", sans-serif;
    display: flex;
    align-items: center;
    justify-content: center;
    gap: 40px;
  }

  .card {
    position: relative;
    width: 540px;
    height: 309px;
    border-radius: 4px;
    overflow: hidden;
    box-shadow: 0 10px 24px rgba(0, 0, 0, 0.35);
    color: var(--white);
  }

  .card__curve {
    position: absolute;
    inset: 0;
    width: 100%;
    height: 100%;
  }

  /* Contact side */
  .card--contact {
    background: linear-gradient(160deg, var(--dark-top) 0%, var(--dark-bottom) 100%);
  }

  .brand {
    position: absolute;
    left: 96px;
    top: 62px;
    display: flex;
    align-items: center;
    gap: 18px;
  }

  .brand__mark {
    width: 64px;
    height: 64px;
    border-radius: 50%;
    background: linear-gradient(160deg, var(--accent-red) 0%, var(--accent-orange) 35%, var(--accent-violet) 70%, var(--accent-cyan) 100%);
    flex: none;
  }

  .brand__name {
    font-size: 34px;
    font-weight: 700;
    letter-spacing: 7px;
    text-transform: uppercase;
    line-height: 1;
  }

  .brand__name small {
    display: block;
    font-size: 13px;
    font-weight: 700;
    letter-spacing: 11px;
    margin-top: 9px;
  }

  .contact {
    position: absolute;
    left: 178px;
    right: 40px;
    top: 158px;
  }

  .contact__name {
    font-size: 19px;
    font-weight: 700;
    text-transform: uppercase;
    letter-spacing: 1px;
    color: var(--accent-violet);
  }

  .contact__title {
    font-size: 14px;
    margin-top: 3px;
  }

  .contact__rule {
    height: 1px;
    background: var(--rule-dark);
    margin: 12px 0 10px;
  }

  .contact__details {
    font-size: 12.5px;
    letter-spacing: 0.3px;
    white-space: nowrap;
  }

  .contact__label { color: var(--accent-orange); }

  /* Product side */
  .card--product {
    background: linear-gradient(150deg, var(--blue-top) 0%, var(--blue-mid) 50%, var(--blue-bottom) 100%);
  }

  .product {
    position: absolute;
    left: 0;
    right: 0;
    top: 44px;
    text-align: center;
  }

  .product__mark {
    display: block;
    width: 64px;
    height: 64px;
    margin: 0 auto 8px;
    border-radius: 50%;
    background: var(--white);
  }

  .product__name {
    font-size: 38px;
    font-weight: 700;
    line-height: 1.1;
  }

  .product__tagline {
    margin-top: 18px;
    font-size: 13.5px;
    letter-spacing: 0.8px;
    text-transform: uppercase;
  }

  .product__rule {
    width: 400px;
    height: 1px;
    background: var(--rule-light);
    margin: 9px auto;
  }

  .product__web {
    font-size: 14px;
    letter-spacing: 0.5px;
  }
</style>
</head>
<body>

  <section class="card card--contact" aria-label="Contact side">
    <svg class="card__curve" viewBox="0 0 540 309" aria-hidden="true">
      <path d="M0 285 C160 255 300 320 540 255" fill="none" stroke="var(--dark-trace)" stroke-width="8"/>
    </svg>

    <div class="brand">
      <span class="brand__mark" role="img" aria-label="Tarnvale brand mark"></span>
      <p class="brand__name">Tarnvale<small>Language</small></p>
    </div>

    <div class="contact">
      <p class="contact__name">Perry Dunmore</p>
      <p class="contact__title">Founder &amp; CEO</p>
      <div class="contact__rule"></div>
      <p class="contact__details">
        <span class="contact__label">P:</span> (555)-014-2286 |
        <span class="contact__label">E:</span> pdunmore@quillpost-mail.net
      </p>
    </div>
  </section>

  <section class="card card--product" aria-label="Product side">
    <svg class="card__curve" viewBox="0 0 540 309" aria-hidden="true">
      <path d="M0 275 C150 245 340 240 540 300" fill="none" stroke="var(--blue-trace)" stroke-width="9"/>
    </svg>

    <div class="product">
      <span class="product__mark" role="img" aria-label="Glimworld product mark"></span>
      <p class="product__name">Glimworld</p>
      <p class="product__tagline">Culturally Immersive Language Learning Games</p>
      <div class="product__rule"></div>
      <p class="product__web">www.glimworld-play.com</p>
    </div>
  </section>

</body>
</html>
```